Design and Renovation Company Luxury Business Card

I want to create a luxury business card for a Design and Renovation Firm . We will use our current logo. The company name is 528BUILDA. We do not want anything standard. We need a very unique concept.
Please see uploaded inspiration. I really like the textured paper option. I would like the card to be thick with debossing, and/or embossing options. The logo has orange in it but I would like to see the card with and without the orange. I think the orange may make the company feel less high-end. The goal is to elevate the logo not match its vibe per se of the logo. We want something very unique, not standard at all!
I would like a space for :
Logo,
Name,
Position,
Email,
Office number,
Website Address,
Business Address,
Thank you!
Have fun!
Target Market(s)
Home owners Age 35 +
Industry/Entity Type
Design and Renovation
Contact Information for Business Card
Logo, Name, Position, Email, Office number, Website Address, Business Address,.
Colors
Designer to choose colors to be used in the design.
Requirements
Must have
- A luxury designer feel. Must be black or dark grey but open to other luxury ideas.
Nice to have
- Gold, silver, black embossing or debossing. Textured paper design.
Should not have
- A cheap look and feel.

```html
<!DOCTYPE html>
<html lang="en">
<head>
<meta charset="utf-8">
<title>528BUILDA Business Card</title>
<link rel="stylesheet" href="https://fonts.googleapis.com/css2?family=Roboto:wght@400;700&display=swap">
<style>
  :root {
    --backdrop: #c9c9c9;
    --card: #121212;
    --card-edge: #1c1c1c;
    --silver: #d6d6d6;
    --silver-soft: #a9a9a9;
    --rule: #3a3a3a;
    --pattern-dark: #050505;
    --pattern-mid: #1d1d1d;
  }
  * { box-sizing: border-box; margin: 0; padding: 0; }
  html, body { width: 1200px; height: 800px; overflow: hidden; }
  body {
    background: var(--backdrop);
    font-family: "Roboto", Arial, sans-serif;
    position: relative;
  }
  .card {
    position: absolute;
    width: 560px;
    height: 320px;
    background: var(--card);
    border: 1px solid var(--card-edge);
    box-shadow: 0 14px 30px rgba(0,0,0,0.28);
    overflow: hidden;
  }
  .card--contact { left: 110px; top: 60px; }
  .card--brand { left: 530px; top: 410px; }

  /* contact side */
  .brand-block {
    position: absolute;
    left: 0; top: 0;
    width: 250px; height: 100%;
    display: flex; flex-direction: column;
    align-items: center; justify-content: center;
    gap: 22px;
  }
  .brand-square {
    width: 110px; height: 110px;
    background: var(--silver-soft);
  }
  .wordmark {
    color: var(--silver);
    font-weight: 400;
    font-size: 30px;
    letter-spacing: 4px;
  }
  .divider {
    position: absolute;
    left: 262px; top: 40px;
    width: 1px; height: 200px;
    background: var(--rule);
  }
  .details {
    position: absolute;
    left: 290px; top: 48px;
    color: var(--silver);
  }
  .person-name {
    font-weight: 700;
    font-size: 20px;
    letter-spacing: 1px;
    text-transform: uppercase;
  }
  .person-role {
    font-size: 14px;
    color: var(--silver-soft);
    margin-top: 3px;
  }
  .contact-list {
    list-style: none;
    margin-top: 22px;
    font-size: 15px;
    line-height: 24px;
  }
  .contact-list li { display: flex; align-items: center; gap: 8px; }
  .contact-list svg { width: 14px; height: 14px; flex: none; }
  .address {
    margin-top: 16px;
    font-size: 15px;
    line-height: 21px;
    color: var(--silver-soft);
    font-style: normal;
  }

  /* brand side */
  .tile-field {
    position: absolute; inset: 0;
    background: radial-gradient(ellipse at 45% 40%, var(--pattern-mid), var(--pattern-dark) 75%);
  }
  .brand-lockup {
    position: absolute;
    left: 150px; top: 118px;
    display: flex; align-items: center; gap: 12px;
  }
  .lockup-square {
    width: 42px; height: 42px;
    background: var(--silver-soft);
  }
  .lockup-text { color: var(--silver); }
  .lockup-name {
    font-size: 34px;
    letter-spacing: 4px;
    line-height: 1;
  }
  .lockup-tagline {
    font-size: 10px;
    font-weight: 700;
    letter-spacing: 1.6px;
    margin-top: 3px;
  }
</style>
</head>
<body>

<section class="card card--contact">
  <div class="brand-block">
    <div class="brand-square"></div>
    <div class="wordmark">528BUILDA</div>
  </div>
  <div class="divider"></div>
  <div class="details">
    <h1 class="person-name">Marcus Hale</h1>
    <p class="person-role">Managing Director</p>
    <ul class="contact-list">
      <li>
        <svg viewBox="0 0 16 16" aria-hidden="true"><path fill="#d6d6d6" d="M3.5 1.5l2.5 0 1 3.5-1.7 1.2a8 8 0 0 0 4.5 4.5L11 9l3.5 1v2.5c0 1-.8 2-2 2A11 11 0 0 1 1.5 3.5c0-1.2 1-2 2-2z"/></svg>
        044-555 010 272
      </li>
      <li>
        <svg viewBox="0 0 16 16" aria-hidden="true"><rect x="1" y="3" width="14" height="10" fill="none" stroke="#d6d6d6" stroke-width="1.5"/><path d="M1 3l7 6 7-6" fill="none" stroke="#d6d6d6" stroke-width="1.5"/></svg>
        hello@528builda.com
      </li>
      <li>
        <svg viewBox="0 0 16 16" aria-hidden="true"><circle cx="8" cy="8" r="6.5" fill="none" stroke="#d6d6d6" stroke-width="1.3"/><ellipse cx="8" cy="8" rx="3" ry="6.5" fill="none" stroke="#d6d6d6" stroke-width="1.1"/><path d="M1.5 8h13M2.5 5h11M2.5 11h11" stroke="#d6d6d6" stroke-width="1"/></svg>
        www.528builda.com
      </li>
    </ul>
    <address class="address">421, Address line goes here<br>45452, Country Name</address>
  </div>
</section>

<section class="card card--brand">
  <div class="tile-field" role="img" aria-label="Embossed grid of small dark square tiles covering the card"></div>
  <div class="brand-lockup">
    <div class="lockup-square"></div>
    <div class="lockup-text">
      <div class="lockup-name">528BUILDA</div>
      <div class="lockup-tagline">Design and Renovation Firm</div>
    </div>
  </div>
</section>

</body>
</html>
```